Norrell Advisory WA Business Card

Create an interesting, eye catching and colourful two sided business card. We are a business consulting operation assisting SME's improve all areas of their business. We provide consulting services to assist SME's to create a culture of continuous improvement, making a positive difference in the business. Our tag line is Small changes, big rewards. We want to create a well recognised, innovative brand that can be continued throughout our website, social media and email correspondence.

Target Market(s)

Small to Medium Enterprise Business Owners

Industry/Entity Type

Business Consultant

Contact Information for Business Card

Name of Business: Norrell Advisory - Steady Steps Real Gains
Derek Holloway Ph 0407385510 Megan Holloway Ph 0407913847
Email norrelladvisorywa@mailbox-example.com
Web address TBA
FaceBook page TBA

BACKSIDE OF CARD

Providing assistance with:

• Organisation & Efficiency
• Revenue generation & Marketing
• Financial Management
• Production quality & delivery
• Systems & Process documentation
• Exit Strategy

Font styles to use
Other font styles liked:
• Calibri

Colors

Designer to choose colors to be used in the design.

Requirements
Must have
• Calibri font

```html
<!DOCTYPE html>
<html lang="en">
<head>
<meta charset="utf-8">
<title>Norrell Advisory WA Business Card</title>
<link rel="stylesheet" href="https://fonts.googleapis.com/css2?family=Carlito:wght@400;700&display=swap">
<style>
  :root {
    --backdrop: #3b322e;
    --card-white: #f7f7f5;
    --card-dark: #2a2a2a;
    --ink: #2b2b2b;
    --ink-soft: #4a4a4a;
    --light-text: #d8d8d8;
    --rule: #8a8a8a;
    --blue: #1f88c9;
    --yellow: #f2b418;
    --red: #e8402f;
    --green: #86be2e;
  }
  * { box-sizing: border-box; margin: 0; padding: 0; }
  html, body {
    width: 1200px; height: 844px; overflow: hidden;
    background: var(--backdrop);
    font-family: "Carlito", sans-serif;
  }
  .sheet { position: relative; width: 1200px; height: 844px; }
  .card {
    position: absolute; top: 262px;
    width: 540px; height: 320px;
    box-shadow: 0 12px 28px rgba(0,0,0,.45);
  }

  /* Front */
  .card-front { left: 45px; background: var(--card-white); color: var(--ink); }
  .contacts { position: absolute; left: 42px; top: 48px; }
  .person { margin-bottom: 14px; }
  .person-name { font-size: 21px; font-weight: 700; letter-spacing: .3px; text-transform: uppercase; }
  .person-phone { display: flex; align-items: center; gap: 6px; font-size: 16px; color: var(--ink-soft); margin-top: 2px; }
  .person-phone svg { width: 12px; height: 12px; }
  .brand {
    position: absolute; right: 40px; top: 78px;
    display: flex; flex-direction: column; align-items: center; gap: 14px;
  }
  .brand-mark { width: 54px; height: 54px; background: var(--blue); }
  .brand-name { font-size: 24px; font-weight: 700; letter-spacing: .5px; text-transform: uppercase; color: var(--ink); }
  .links { position: absolute; left: 42px; bottom: 30px; font-size: 16px; color: var(--ink-soft); line-height: 1.55; }
  .links .web { color: var(--blue); font-weight: 700; font-size: 17px; }

  /* Back */
  .card-back { left: 615px; background: var(--card-dark); color: var(--light-text); text-align: center; }
  .back-title { margin-top: 62px; font-size: 32px; font-weight: 700; letter-spacing: 1px; text-transform: uppercase; color: #e6e6e6; }
  .tagline { margin-top: 4px; font-size: 19px; font-weight: 700; letter-spacing: 1px; text-transform: uppercase; }
  .tag-one { color: var(--yellow); }
  .tag-two { color: var(--blue); }
  .tag-three { color: var(--red); }
  .tag-four { color: var(--green); }
  .services-head {
    display: flex; align-items: center; gap: 12px;
    margin: 34px 36px 10px;
    font-size: 14px; font-weight: 700; letter-spacing: 1px; text-transform: uppercase;
  }
  .services-head::before, .services-head::after { content: ""; flex: 1; height: 1px; background: var(--rule); }
  .services { list-style: none; font-size: 15.5px; line-height: 1.35; }
</style>
</head>
<body>
<main class="sheet">
  <section class="card card-front" aria-label="Business card front">
    <div class="contacts">
      <div class="person">
        <div class="person-name">Derek Holloway</div>
        <div class="person-phone">
          <svg viewBox="0 0 24 24" aria-hidden="true"><path fill="#1f88c9" d="M6.6 10.8a15.1 15.1 0 0 0 6.6 6.6l2.2-2.2a1 1 0 0 1 1-.25 11.4 11.4 0 0 0 3.6.57 1 1 0 0 1 1 1V20a1 1 0 0 1-1 1A17 17 0 0 1 3 4a1 1 0 0 1 1-1h3.5a1 1 0 0 1 1 1c0 1.25.2 2.45.57 3.57a1 1 0 0 1-.25 1z"/></svg>
          0407385510
        </div>
      </div>
      <div class="person">
        <div class="person-name">Megan Holloway</div>
        <div class="person-phone">
          <svg viewBox="0 0 24 24" aria-hidden="true"><path fill="#1f88c9" d="M6.6 10.8a15.1 15.1 0 0 0 6.6 6.6l2.2-2.2a1 1 0 0 1 1-.25 11.4 11.4 0 0 0 3.6.57 1 1 0 0 1 1 1V20a1 1 0 0 1-1 1A17 17 0 0 1 3 4a1 1 0 0 1 1-1h3.5a1 1 0 0 1 1 1c0 1.25.2 2.45.57 3.57a1 1 0 0 1-.25 1z"/></svg>
          0407913847
        </div>
      </div>
    </div>

    <div class="brand">
      <div class="brand-mark" aria-hidden="true"></div>
      <div class="brand-name">Norrell Advisory</div>
    </div>

    <div class="links">
      <div>pagelink.example/norrelladvisory</div>
      <div>norrelladvisorywa@mailbox-example.com</div>
      <div class="web">www.norrelladvisory.example</div>
    </div>
  </section>

  <section class="card card-back" aria-label="Business card back">
    <h1 class="back-title">Norrell Advisory</h1>
    <p class="tagline">
      <span class="tag-one">Steady</span>
      <span class="tag-two">Steps</span>
      <span class="tag-three">Real</span>
      <span class="tag-four">Gains</span>
    </p>
    <h2 class="services-head">Providing assistance with</h2>
    <ul class="services">
      <li>Organisation &amp; Efficiency • Revenue generation &amp; Marketing</li>
      <li>Financial Management • Production quality &amp; delivery</li>
      <li>Systems &amp; Process documentation • Exit Strategy</li>
    </ul>
  </section>
</main>
</body>
</html>
```